Cedarvale Ridge College

We are looking to update our current webpage at www.cedarvaleridge.ca. We would like to make it modern, fresh and appealing to students. We want to keep our logo the same with the logo colours blended in as the primary colours and focus. We are open to reconfiguring content as well.
Reason: Hi, In the next 3 days we will have narrowed our search to 3 designs and will make a choice before the final deadline...
College

```html
<!DOCTYPE html>
<html lang="en">
<head>
<meta charset="utf-8">
<title>Cedarvale Ridge College</title>
<link href="https://fonts.googleapis.com/css2?family=Open+Sans:wght@400;600;700&family=Libre+Baskerville:wght@400;700&display=swap" rel="stylesheet">
<style>
:root{
  --navy:#1c2d57;
  --navy-dark:#14213f;
  --green:#2d6a4a;
  --green-bright:#3c8a3e;
  --teal-dark:#0c3b38;
  --teal:#145a50;
  --orange:#f39a1c;
  --grey-band:#e4e4e4;
  --text:#4a4a4a;
  --muted:#7a7a7a;
  --white:#ffffff;
}
*{box-sizing:border-box;margin:0;padding:0}
html,body{width:711px;height:1200px;overflow:hidden}
body{font-family:"Open Sans",Arial,sans-serif;color:var(--text);background:var(--white);position:relative}

/* header */
.site-header{position:absolute;top:0;left:0;width:711px;height:86px;background:var(--white)}
.brand{position:absolute;left:16px;top:16px;display:flex;align-items:center;gap:10px}
.brand-dot{width:34px;height:34px;border-radius:50%;background:var(--navy)}
.brand-name{font-family:"Libre Baskerville",Georgia,serif;font-weight:700;font-size:19px;line-height:1.15;color:var(--navy);width:170px}
.utility-bar{position:absolute;right:0;top:0;width:300px;height:22px;background:var(--navy);display:flex;justify-content:flex-end;align-items:center;gap:16px;padding-right:18px}
.utility-bar a{color:var(--white);font-size:10px;font-weight:600;text-decoration:none;letter-spacing:.5px}
.call-line{position:absolute;right:118px;top:38px;display:flex;align-items:center;gap:6px;color:var(--navy);font-weight:700;font-size:15px;white-space:nowrap}
.apply-btn{position:absolute;right:16px;top:36px;width:92px;height:26px;background:var(--orange);color:var(--white);font-weight:700;font-size:12px;display:flex;align-items:center;justify-content:center;border-radius:2px}

.main-nav{position:absolute;top:86px;left:0;width:711px;height:24px;background:var(--green);display:flex;justify-content:space-around;align-items:center;padding:0 10px}
.main-nav a{color:var(--white);font-size:10px;font-weight:600;text-decoration:none;white-space:nowrap}

/* hero */
.hero{position:absolute;top:110px;left:0;width:711px;height:246px}
.hero-photo{position:absolute;inset:0;background:linear-gradient(100deg,#6d5a4c 0%,#9b8a78 25%,#7f8f6a 50%,#4e6a3c 75%,#2f4a28 100%)}
.hero-panel{position:absolute;left:380px;top:48px;width:300px;padding:12px 14px;background:rgba(255,255,255,.82)}
.hero-title{font-family:"Libre Baskerville",Georgia,serif;font-weight:700;font-size:18px;line-height:1.25;color:#1a1a1a}
.hero-sub{font-family:"Libre Baskerville",Georgia,serif;font-weight:700;font-size:14px;line-height:1.35;color:var(--green-bright);margin-top:6px}
.join-btn{display:inline-block;margin-top:10px;background:var(--green);color:var(--white);font-weight:700;font-size:14px;padding:6px 14px;letter-spacing:.5px}
.hero-edge{position:absolute;left:0;bottom:-4px;width:711px;height:4px;background:var(--navy)}

/* welcome */
.welcome{position:absolute;top:372px;left:16px;width:679px;height:150px}
.welcome h1{font-size:21px;font-weight:600;color:var(--navy)}
.welcome h1 span{color:var(--green)}
.welcome p{width:455px;font-size:9.5px;line-height:1.55;margin-top:8px;color:var(--text)}
.read-btn{display:inline-block;margin-top:8px;background:var(--navy);color:var(--white);font-size:10px;font-weight:600;padding:4px 10px}
.video{position:absolute;right:0;top:4px;width:196px;height:134px;background:linear-gradient(135deg,#b9b2a8,#6d6660)}
.video-play{position:absolute;left:82px;top:44px;width:34px;height:34px;border-radius:50%;background:#d63a2f;display:flex;align-items:center;justify-content:center}
.video-bar{position:absolute;left:0;bottom:0;width:100%;height:14px;background:rgba(0,0,0,.75)}

/* feature band */
.features{position:absolute;top:540px;left:0;width:711px;height:216px;background:var(--grey-band)}
.feature-row{position:absolute;left:34px;top:16px;width:643px;display:flex;gap:11px}
.feature-card{width:152px;background:var(--white)}
.feature-photo{height:88px}
.feature-title{background:var(--navy);color:var(--white);font-size:11px;font-weight:600;text-align:center;padding:5px 0;white-space:nowrap}
.feature-card p{font-size:9px;line-height:1.5;text-align:center;padding:6px 8px 10px}
.arrow{position:absolute;top:84px;width:18px;height:28px;background:var(--navy);display:flex;align-items:center;justify-content:center}
.arrow.left{left:8px}.arrow.right{right:8px}

/* info boxes */
.info-row{position:absolute;top:770px;left:16px;width:679px;display:flex;gap:12px}
.info-box{width:218px;height:168px;border:1px solid #d6d6d6;background:var(--white);position:relative}
.info-head{height:24px;background:var(--navy);color:var(--white);font-size:11px;font-weight:600;display:flex;align-items:center;gap:7px;padding-left:10px}
.team-photo{margin:8px;height:72px;background:linear-gradient(120deg,#c8bfb4,#8a9aa8)}
.info-box p{font-size:9px;line-height:1.5;padding:0 8px}
.info-box .read-btn{margin:5px 8px 0}
.news-item{display:flex;gap:8px;padding:10px 8px 0}
.news-item p{padding:0}
.date{width:34px;flex:none;text-align:center;border:1px solid var(--navy)}
.date b{display:block;background:var(--navy);color:var(--white);font-size:12px;padding:1px 0}
.date span{font-size:9px;color:var(--navy);font-weight:600}
.info-box .quote{font-style:italic;padding:12px 10px 0}
.student{display:flex;align-items:center;justify-content:flex-end;gap:8px;padding:10px 10px 0;font-size:10px;font-weight:600;color:var(--navy)}
.avatar{width:30px;height:30px;border-radius:50%;background:linear-gradient(135deg,#b7a694,#6d5d50)}

/* footer */
.footer-mark{position:absolute;top:952px;left:0;width:711px;font-family:"Libre Baskerville",Georgia,serif;font-weight:700;font-size:20px;color:var(--navy);display:flex;justify-content:center;align-items:center;gap:10px}
.footer-mark i{width:26px;height:26px;border-radius:50%;background:var(--navy);display:inline-block}
.footer-wave{position:absolute;top:985px;left:0}
.site-footer{position:absolute;top:1040px;left:0;width:711px;height:140px;background:var(--teal-dark);display:flex;padding:12px 16px 0;gap:16px;color:#cfe0dc}
.site-footer h4{color:var(--white);font-size:10px;font-weight:700;letter-spacing:.5px;margin-bottom:8px;white-space:nowrap}
.foot-col{font-size:8.5px;line-height:1.7}
.links{display:grid;grid-template-columns:auto auto;column-gap:10px;width:180px;white-space:nowrap}
.contact-line{display:flex;align-items:center;gap:5px;white-space:nowrap}
.field{width:130px;height:14px;background:var(--white);color:var(--muted);font-size:8px;padding-left:4px;margin-top:4px;line-height:14px}
.sub-btn{display:inline-block;margin-top:5px;background:var(--navy);color:var(--white);font-size:8.5px;font-weight:600;padding:2px 8px}
.social{display:flex;align-items:center;gap:6px;margin-bottom:6px;color:var(--white);font-weight:600;white-space:nowrap}
.social i{width:16px;height:16px;border-radius:50%;background:var(--teal);border:1px solid #6fa59a;display:inline-block}
.copyright{position:absolute;top:1180px;left:0;width:711px;height:20px;background:var(--navy-dark);color:#c9d2e2;font-size:8.5px;text-align:center;line-height:20px}
</style>
</head>
<body>

<header class="site-header">
  <div class="brand"><span class="brand-dot"></span><span class="brand-name">Cedarvale Ridge College</span></div>
  <nav class="utility-bar"><a href="#">DONATE</a><a href="#">LIBRARY</a><a href="#">TEXT FOR INFO</a></nav>
  <div class="call-line">
    <svg width="16" height="16" viewBox="0 0 24 24"><path fill="#1c2d57" d="M6.6 10.8a15 15 0 0 0 6.6 6.6l2.2-2.2a1 1 0 0 1 1-.25 11.4 11.4 0 0 0 3.6.57 1 1 0 0 1 1 1V20a1 1 0 0 1-1 1A17 17 0 0 1 3 4a1 1 0 0 1 1-1h3.5a1 1 0 0 1 1 1c0 1.25.2 2.45.57 3.57a1 1 0 0 1-.25 1z"/></svg>
    0198-765-432
  </div>
  <div class="apply-btn">Apply Today</div>
</header>

<nav class="main-nav">
  <a href="#">About Us</a><a href="#">Consider Cedarvale</a><a href="#">Current Student</a><a href="#">Alumni</a><a href="#">Supporters</a><a href="#">News &amp; Events</a><a href="#">Cedarvale Park</a><a href="#">Contact Us</a>
</nav>

<section class="hero">
  <div class="hero-photo" role="img" aria-label="Students walking across a leafy college campus"></div>
  <div class="hero-panel">
    <div class="hero-title">EDUCATING, EDUIPPING &amp; ENRICHING</div>
    <div class="hero-sub">Christians For Spirit-empowered Ministry In The Church &amp; In The World</div>
    <div class="join-btn">JOIN NOW</div>
  </div>
  <div class="hero-edge"></div>
</section>

<section class="welcome">
  <h1>Welcome To <span>Cedarvale Ridge College</span></h1>
  <p>Our campus brings students together to study, grow and serve. We offer degree and diploma programs shaped by faith, practical ministry training and close mentoring from caring faculty. Classes are small, community life is warm and every student is known by name. Come visit, meet our people and discover where your calling can lead you next.</p>
  <span class="read-btn">Read More</span>
  <div class="video" role="img" aria-label="Video preview of a campus lecture">
    <div class="video-play"><svg width="14" height="14" viewBox="0 0 10 10"><path d="M2 1l7 4-7 4z" fill="#fff"/></svg></div>
    <div class="video-bar"></div>
  </div>
</section>

<section class="features">
  <div class="arrow left"><svg width="8" height="12" viewBox="0 0 8 12"><path d="M7 1L2 6l5 5" stroke="#fff" stroke-width="2" fill="none"/></svg></div>
  <div class="feature-row">
    <article class="feature-card">
      <div class="feature-photo" role="img" aria-label="Student holding books" style="background:linear-gradient(135deg,#5a7fb0,#a33f3f)"></div>
      <div class="feature-title">Admissions Information</div>
      <p>Learn how to apply, key dates and the steps to join us.</p>
    </article>
    <article class="feature-card">
      <div class="feature-photo" role="img" aria-label="Campus building exterior" style="background:linear-gradient(135deg,#8fb3c9,#5d7d4c)"></div>
      <div class="feature-title">Campus Directory</div>
      <p>Find offices, classrooms, housing and staff contacts across our campus.</p>
    </article>
    <article class="feature-card">
      <div class="feature-photo" role="img" aria-label="Students gathered in a program session" style="background:linear-gradient(135deg,#3f5d8a,#6d8fa8)"></div>
      <div class="feature-title">Our Programme</div>
      <p>Explore degrees, diplomas and certificates in ministry and leadership.</p>
    </article>
    <article class="feature-card">
      <div class="feature-photo" role="img" aria-label="Student reading the course catalogue" style="background:linear-gradient(135deg,#c9c3bb,#7d8ea3)"></div>
      <div class="feature-title">Download Catalogue</div>
      <p>Get the full course catalogue with fees and program details.</p>
    </article>
  </div>
  <div class="arrow right"><svg width="8" height="12" viewBox="0 0 8 12"><path d="M1 1l5 5-5 5" stroke="#fff" stroke-width="2" fill="none"/></svg></div>
</section>

<section class="info-row">
  <div class="info-box">
    <div class="info-head"><svg width="12" height="12" viewBox="0 0 12 12"><circle cx="6" cy="4" r="2.5" fill="#fff"/><path d="M1 12c0-3 2.2-5 5-5s5 2 5 5z" fill="#fff"/></svg>Meet Our Team</div>
    <div class="team-photo" role="img" aria-label="Group photo of faculty and staff"></div>
    <p>Meet the faculty and staff who guide students in study and life.</p>
    <span class="read-btn">Read More</span>
  </div>
  <div class="info-box">
    <div class="info-head"><svg width="12" height="12" viewBox="0 0 12 12"><rect x="1" y="2" width="10" height="9" fill="none" stroke="#fff"/><path d="M1 5h10" stroke="#fff"/></svg>News &amp; Events</div>
    <div class="news-item"><div class="date"><b>21</b><span>Nov</span></div><p>Spring open house welcomes new students to campus.</p></div>
    <div class="news-item"><div class="date"><b>21</b><span>Nov</span></div><p>Chapel choir announces its winter concert dates.</p></div>
  </div>
  <div class="info-box">
    <div class="info-head"><svg width="12" height="12" viewBox="0 0 12 12"><path d="M1 2h10v6H5l-3 3V8H1z" fill="#fff"/></svg>Student Testimonials</div>
    <p class="quote">My years here shaped my faith and gave me friends and mentors for life. I felt ready to serve from day one.</p>
    <div class="student">Anna Reyes<span class="avatar" role="img" aria-label="Student portrait"></span></div>
  </div>
</section>

<div class="footer-mark"><i></i>Cedarvale Ridge College</div>
<svg class="footer-wave" width="711" height="56" viewBox="0 0 711 56">
  <path d="M0 30 C180 -6 420 60 711 14 L711 56 L0 56Z" fill="#2d6a4a"/>
  <path d="M0 42 C200 14 430 66 711 28 L711 56 L0 56Z" fill="#0c3b38"/>
</svg>

<footer class="site-footer">
  <div class="foot-col" style="width:180px">
    <h4>QUICK LINKS</h4>
    <div class="links"><span>› Home</span><span>› Supporters</span><span>› About Us</span><span>› News &amp; Events</span><span>› Consider Cedarvale</span><span>› Cedarvale Park</span><span>› Current Student</span><span>› Contact</span><span>› Alumni</span></div>
  </div>
  <div class="foot-col" style="width:150px">
    <h4>CONTACT ADDRESS</h4>
    <div class="contact-line"><svg width="9" height="11" viewBox="0 0 10 12"><path d="M5 0a4 4 0 0 1 4 4c0 3-4 8-4 8S1 7 1 4a4 4 0 0 1 4-4z" fill="#cfe0dc"/></svg>4210 Ridge Road, Cedarvale,</div>
    <div style="padding-left:14px">BC V2X 1A1</div>
    <div class="contact-line"><svg width="9" height="9" viewBox="0 0 24 24"><path fill="#cfe0dc" d="M6.6 10.8a15 15 0 0 0 6.6 6.6l2.2-2.2 4.6 1.3V21A17 17 0 0 1 3 4h4.5l1.3 4.6z"/></svg>604-555-0142</div>
    <div class="contact-line"><svg width="9" height="9" viewBox="0 0 24 24"><path fill="#cfe0dc" d="M6.6 10.8a15 15 0 0 0 6.6 6.6l2.2-2.2 4.6 1.3V21A17 17 0 0 1 3 4h4.5l1.3 4.6z"/></svg>604-555-0178</div>
    <div class="contact-line"><svg width="10" height="8" viewBox="0 0 10 8"><rect width="10" height="8" fill="#cfe0dc"/><path d="M0 0l5 4 5-4" stroke="#0c3b38" fill="none"/></svg>info@cedarvaleridge.ca</div>
  </div>
  <div class="foot-col" style="width:160px">
    <h4>NEWSLETTER SIGNUP</h4>
    <div>Sign up with us and get updates in your inbox.</div>
    <div class="field">Your Name</div>
    <div class="field">Email Address</div>
    <span class="sub-btn">Subscribe</span>
  </div>
  <div class="foot-col">
    <h4>SOCIAL CONNECT</h4>
    <div class="social"><i></i>Community Page</div>
    <div class="social"><i></i>Photo Stream</div>
    <div class="social"><i></i>Latest Posts</div>
  </div>
</footer>
<div class="copyright">© 2014 Cedarvale Ridge | All rights reserved</div>

</body>
</html>
```